Business Card Design of an established Waste Management, Plastic Recycling and Renewable Energy Comp

We are looking for business card design for plastic card with holograms (Very similar to credit card). I will provide our logo (Quenbys). So the name on the business card will be our logo )Quenbys) + Environmental next to it, so it will read Quenbys Environmental. The font for Environmental does not to be the same as the font of the logo. The holograms will be used to display ISO14001 Certified (In normal credit card, normally on the holograms, they show nova or kelo). I will post the design requirements from the card printing company very shortly to make sure they can use the design for the plastic card.

Target Market(s)

Companies, Government Organizations, Corporations.

Industry/Entity Type

Business

Contact Information for Business Card

Motto (Under the logo): Doing It Properly
Name: Leopold Maresca; Position: Business Manager; Address: Pelmore Resource & Sorting Depot, Tressingham Rd, Brennick Vale, NL 4810; Ph: +61 8 5210 4738; Mob: +61 455 903 172; E: Leo@quenbysenvironmental-mail.com

Requirements
Must have
• Business Names: Quenbys Logo + Environmental word after the logo.
• Motto (Under the logo): Doing It Properly
• All the Business Card Details above.
• Hologram Logo on the lower right corner which says: ISO 14001 Certified.
• Please remember the design will be printed on plastic card Not paper. The plastic crad is the same as credit card. Hope this helps. Thank You

```html
<!DOCTYPE html>
<html lang="en">
<head>
<meta charset="utf-8">
<title>Quenbys Environmental — Business Card</title>
<link rel="stylesheet" href="https://fonts.googleapis.com/css2?family=Source+Sans+3:wght@400;600&display=swap">
<style>
  :root {
    --stage-top: #e4e4e4;
    --stage-bottom: #cdcdcd;
    --card-center: #2a2a2a;
    --card-edge: #0b0b0b;
    --accent: #2e9fe0;
    --logo-grey: #6d6d6d;
    --text: #ffffff;
    --rule: #3a3a3a;
  }
  * { margin: 0; padding: 0; box-sizing: border-box; }
  html, body { width: 1200px; height: 900px; overflow: hidden; }
  body {
    position: relative;
    background: linear-gradient(180deg, var(--stage-top), var(--stage-bottom));
    font-family: "Source Sans 3", "Myriad Pro", sans-serif;
    color: var(--text);
  }
  .card {
    position: absolute;
    top: 306px;
    width: 440px;
    height: 271px;
    border-radius: 10px;
    background: radial-gradient(ellipse at 50% 35%, var(--card-center), var(--card-edge) 75%);
    box-shadow: 0 2px 6px rgba(0,0,0,.25);
    overflow: hidden;
  }
  .card--front { left: 149px; }
  .card--back { left: 608px; }

  .brand { position: absolute; display: flex; align-items: flex-start; }
  .brand__mark { flex: none; border-radius: 50%; }
  .brand__words { display: flex; flex-direction: column; }
  .brand__name { font-weight: 600; line-height: 1; }
  .brand__sub { text-transform: uppercase; line-height: 1; }
  .brand__motto { text-transform: uppercase; line-height: 1; }

  .card--front .brand { right: 31px; top: 52px; gap: 10px; }
  .card--front .brand__mark { width: 56px; height: 56px; background: var(--accent); }
  .card--front .brand__name { font-size: 38px; color: var(--logo-grey); }
  .card--front .brand__sub { font-size: 11px; letter-spacing: 1px; color: var(--accent); margin-top: 3px; }
  .card--front .brand__motto { font-size: 7px; letter-spacing: 3.4px; color: var(--accent); margin-top: 3px; }

  .card--back .brand { left: 68px; top: 98px; gap: 14px; }
  .card--back .brand__mark { width: 80px; height: 80px; background: var(--text); }
  .card--back .brand__name { font-size: 56px; color: var(--text); }
  .card--back .brand__sub { font-size: 16px; letter-spacing: 1.3px; color: var(--text); margin-top: 0; }
  .card--back .brand__motto { font-size: 9.5px; letter-spacing: 4px; color: var(--text); margin-top: 5px; }

  .holder { position: absolute; left: 28px; top: 145px; right: 30px; }
  .holder__name { display: flex; align-items: center; gap: 8px; font-size: 15px; font-weight: 600; color: var(--accent); }
  .holder__name::after { content: ""; flex: 1; height: 1px; background: var(--rule); }
  .holder__role { font-size: 12.5px; margin-top: 1px; }

  .cert-badge {
    position: absolute; left: 29px; top: 194px;
    width: 67px; height: 54px;
    border: 1.5px solid var(--text); border-radius: 5px;
    display: flex; align-items: center; justify-content: center;
  }
  .cert-badge span { width: 40px; height: 40px; border: 1.2px solid var(--text); border-radius: 50%; }

  .contact { position: absolute; right: 30px; top: 161px; text-align: right; font-size: 12.5px; line-height: 18px; list-style: none; }
  .contact li { display: flex; justify-content: flex-end; align-items: center; gap: 5px; }
  .contact svg { width: 9px; height: 9px; fill: var(--accent); }
  .address { position: absolute; right: 30px; top: 219px; text-align: right; font-size: 12.5px; line-height: 16px; font-style: normal; }
</style>
</head>
<body>
  <section class="card card--front" aria-label="Business card front">
    <div class="brand">
      <span class="brand__mark"></span>
      <div class="brand__words">
        <span class="brand__name">Quenbys</span>
        <span class="brand__sub">Environmental</span>
        <span class="brand__motto">Doing It Properly</span>
      </div>
    </div>

    <div class="holder">
      <p class="holder__name">Leopold Maresca</p>
      <p class="holder__role">Business Manager</p>
    </div>

    <div class="cert-badge" role="img" aria-label="Certification hologram"><span></span></div>

    <ul class="contact">
      <li>+61 8 5210 4738
        <svg viewBox="0 0 10 10"><path d="M2 0.5l2 2-1 1.2c.6 1.3 1.5 2.2 2.8 2.8L7 5.5l2 2-1.3 1.8C4 9 1 6 .7 1.8z"/></svg></li>
      <li>+61 455 903 172
        <svg viewBox="0 0 10 10"><path d="M2.5 0h5v10h-5zM3.5 1v7h3V1z"/></svg></li>
      <li>Leo@quenbysenvironmental-mail.com
        <svg viewBox="0 0 10 10"><path d="M0 2h10v6H0zM1 2.8l4 2.7 4-2.7V2.5H1z"/></svg></li>
    </ul>

    <address class="address">Pelmore Resource &amp; Sorting<br>Depot Tressingham Rd, Brennick Vale, NL 4810</address>
  </section>

  <section class="card card--back" aria-label="Business card back">
    <div class="brand">
      <span class="brand__mark"></span>
      <div class="brand__words">
        <span class="brand__name">Quenbys</span>
        <span class="brand__sub">Environmental</span>
        <span class="brand__motto">Doing It Properly</span>
      </div>
    </div>
  </section>
</body>
</html>
```